Computer Training in the Education sector - Letterhead

We need a new letter head to be designed for the company. We provide computer training fro the Education Sector, both primary and private tertiary providers. The colours will need to tie in with the website www.crossingthestream.co.nz.
The company name is Crossing the Stream with the tag line of Computer Training for Educators.
The footer will need to have the following detail...
0508 PCS MENTOR
021 839 415
www.crossingthestream.co.nz / training@crossingthestream.co.nz
Updates

Thanks for the designs so far.

Some have watermarks in the background. Please don't worry about using watermarks as I will not be using a watermark in in a final design.
Regards,
Roger

Thank you for all the designs and the effort. There was some great concepts that came through.

Cheers
Roger

Industry/Entity Type

Computer

```html
<!DOCTYPE html>
<html lang="en">
<head>
<meta charset="utf-8">
<title>Crossing the Stream – Letterhead</title>
<link rel="stylesheet" href="https://fonts.googleapis.com/css2?family=Open+Sans:wght@400;600&display=swap">
<style>
  :root {
    --paper: #ffffff;
    --brand-blue: #2f6db5;
    --brand-orange: #ee9a45;
    --brand-green: #8fbf48;
    --ink: #111111;
  }
  * { margin: 0; padding: 0; box-sizing: border-box; }
  html, body {
    width: 848px;
    height: 1200px;
    overflow: hidden;
    background: var(--paper);
  }
  .letterhead {
    position: relative;
    width: 848px;
    height: 1200px;
    background: var(--paper);
    font-family: "Open Sans", Arial, sans-serif;
    overflow: hidden;
  }
  .accent {
    position: absolute;
    border-radius: 40%;
  }
  .accent--top-left {
    left: -30px; top: 20px; width: 130px; height: 80px;
    background: radial-gradient(ellipse at 40% 50%, rgba(143,191,72,0.85), rgba(143,191,72,0) 70%);
  }
  .accent--top-centre {
    left: 215px; top: -20px; width: 250px; height: 175px;
    background: radial-gradient(ellipse at 55% 45%, rgba(238,154,69,0.85), rgba(238,154,69,0) 70%);
  }
  .accent--bottom-blue {
    left: 470px; top: 1105px; width: 240px; height: 120px;
    background: radial-gradient(ellipse at 45% 60%, rgba(47,109,181,0.85), rgba(47,109,181,0) 70%);
  }
  .accent--bottom-green {
    left: 700px; top: 980px; width: 190px; height: 240px;
    background: radial-gradient(ellipse at 65% 55%, rgba(143,191,72,0.85), rgba(143,191,72,0) 70%);
  }
  .brand {
    position: absolute;
    right: 118px;
    top: 60px;
    display: flex;
    align-items: center;
    gap: 10px;
  }
  .brand__mark {
    width: 14px; height: 14px;
    border-radius: 50%;
    background: var(--brand-blue);
  }
  .brand__name {
    font-size: 24px;
    font-weight: 600;
    color: var(--brand-blue);
    line-height: 1.1;
  }
  .tagline {
    position: absolute;
    right: 118px;
    top: 176px;
    text-align: right;
    color: var(--brand-blue);
    font-size: 17px;
    line-height: 26px;
    letter-spacing: 0.5px;
  }
  .contact {
    position: absolute;
    left: 70px;
    top: 1070px;
    list-style: none;
    color: var(--ink);
    font-size: 15px;
    font-weight: 600;
    letter-spacing: 0.6px;
    line-height: 22px;
  }
  .contact__gap { margin-top: 6px; }
</style>
</head>
<body>
  <main class="letterhead">
    <div class="accent accent--top-left" role="img" aria-label="Green tile pattern accent"></div>
    <div class="accent accent--top-centre" role="img" aria-label="Orange tile pattern accent"></div>
    <div class="accent accent--bottom-blue" role="img" aria-label="Blue tile pattern accent"></div>
    <div class="accent accent--bottom-green" role="img" aria-label="Green tile pattern accent"></div>

    <header>
      <div class="brand">
        <span class="brand__mark"></span>
        <span class="brand__name">Crossing the Stream</span>
      </div>
      <p class="tagline">Crossing the Stream<br>Computer training for Educators</p>
    </header>

    <footer>
      <ul class="contact">
        <li>0508 PCS MENTOR</li>
        <li>021 839 415</li>
        <li class="contact__gap">training@crossingthestream.co.nz</li>
        <li>www.crossingthestream.co.nz</li>
      </ul>
    </footer>
  </main>
</body>
</html>
```